Im open to ideas.. I was thinking on my business cards aswell as my logo. a place for my name. email. phone number and abn..

ive attched a file with my business logo. which i dont love the colours.. i was think a dark background with charcoal letters so something along those colour schumes but im open to ideas..

BRM Constructions

```html
<!DOCTYPE html>
<html lang="en">
<head>
<meta charset="utf-8">
<title>BRM Constructions – Business Card</title>
<link rel="stylesheet" href="https://fonts.googleapis.com/css2?family=Michroma&display=swap">
<style>
  :root {
    --backdrop: #7f7f7f;
    --card-white: #ffffff;
    --charcoal: #3d3d3d;
    --wordmark: #3a3a3a;
    --text-light: #ffffff;
  }
  html, body {
    margin: 0;
    padding: 0;
    width: 1200px;
    height: 852px;
    overflow: hidden;
    background: var(--backdrop);
  }
  .canvas {
    position: relative;
    width: 1200px;
    height: 852px;
  }
  .business-card {
    position: absolute;
    left: 232px;
    top: 186px;
    width: 760px;
    height: 464px;
    border-radius: 22px;
    overflow: hidden;
    background: var(--card-white);
    font-family: "Michroma", sans-serif;
  }
  .brand-area {
    position: absolute;
    left: 0;
    top: 0;
    width: 100%;
    height: 276px;
    display: flex;
    align-items: center;
    justify-content: center;
  }
  .brand-name {
    margin: 40px 0 0;
    font-size: 34px;
    font-weight: 400;
    letter-spacing: 2px;
    color: var(--wordmark);
    white-space: nowrap;
  }
  .contact-band {
    position: absolute;
    left: 0;
    top: 276px;
    width: 100%;
    height: 188px;
    background: var(--charcoal);
    color: var(--text-light);
  }
  .person-name {
    position: absolute;
    left: 43px;
    top: 116px;
    margin: 0;
    font-size: 23px;
    font-weight: 400;
    letter-spacing: 0.5px;
  }
  .contact-list {
    position: absolute;
    right: 36px;
    top: 38px;
    margin: 0;
    padding: 0;
    list-style: none;
    font-size: 17px;
    letter-spacing: 0.5px;
  }
  .contact-item {
    display: flex;
    align-items: center;
    justify-content: flex-end;
    height: 42px;
  }
  .contact-item .icon {
    width: 28px;
    height: 34px;
    margin-left: 18px;
    display: flex;
    align-items: center;
    justify-content: center;
  }
  .contact-item.abn {
    margin-right: 46px;
  }
</style>
</head>
<body>
<main class="canvas">
  <section class="business-card">
    <header class="brand-area">
      <h1 class="brand-name">BRM CONSTRUCTIONS</h1>
    </header>
    <div class="contact-band">
      <p class="person-name">YOUR NAME</p>
      <ul class="contact-list">
        <li class="contact-item abn">ABN 12 345 678 910</li>
        <li class="contact-item phone">
          <span>0400 000 000</span>
          <span class="icon">
            <svg width="20" height="34" viewBox="0 0 20 34" aria-hidden="true">
              <rect x="1.5" y="1.5" width="17" height="31" rx="3" fill="none" stroke="#ffffff" stroke-width="2"/>
              <line x1="1.5" y1="6" x2="18.5" y2="6" stroke="#ffffff" stroke-width="1.5"/>
              <line x1="1.5" y1="27" x2="18.5" y2="27" stroke="#ffffff" stroke-width="1.5"/>
            </svg>
          </span>
        </li>
        <li class="contact-item email">
          <span>EMAIL@EMAIL.COM.AU</span>
          <span class="icon">
            <svg width="28" height="20" viewBox="0 0 28 20" aria-hidden="true">
              <rect x="0" y="0" width="28" height="20" fill="#ffffff"/>
              <polyline points="0,0 14,11 28,0" fill="none" stroke="#3d3d3d" stroke-width="1.6"/>
            </svg>
          </span>
        </li>
      </ul>
    </div>
  </section>
</main>
</body>
</html>
```